Eye Catching Business Card for Optometrist

We've recently refreshed our logo and now we need a fresh and bold look for our business cards. We provide progressive ways to improve people's vision and protect their eye health.

Use our new logo as guidance into the colors to use. As far as style goes, I love how bold and eye catching the card is for Lanternfield Studio. Feel free to use your creative judgement.

Tagline: "Clearly the best for your vision."

pertinent info to include:

Dr. Marcus Velbrin
Optometrist

7258 Dunmore Ridge Blvd #215
Brantwell, MO 64172
(555) 382-9017

marc@brantwellfamilyeyecare.example
www.brantwellfamilyeyecare.example

```html
<!DOCTYPE html>
<html lang="en">
<head>
<meta charset="utf-8">
<title>Brantwell Family Eye Care – Business Cards</title>
<link rel="stylesheet" href="https://fonts.googleapis.com/css2?family=Michroma&family=Open+Sans:wght@400;600;700&display=swap">
<style>
  :root {
    --page: #e9e7e4;
    --card-light: #f4f4f4;
    --card-shade: #d9d9da;
    --tan: #d6bf9d;
    --red: #c9363e;
    --ink: #2b2b2b;
    --ink-soft: #555555;
    --white: #ffffff;
  }
  * { box-sizing: border-box; margin: 0; padding: 0; }
  html, body {
    width: 1200px; height: 906px; overflow: hidden;
    background: var(--page);
    font-family: "Open Sans", Arial, sans-serif;
  }
  .canvas { position: relative; width: 1200px; height: 906px; }

  .card {
    position: absolute; width: 700px; height: 400px; overflow: hidden;
    box-shadow: 0 10px 28px rgba(0,0,0,.18);
  }
  .card--back { left: 90px; top: 50px; }
  .card--front { left: 410px; top: 456px; }

  .card__light {
    position: absolute; left: 0; top: 0; width: 100%;
    background: linear-gradient(180deg, var(--card-light) 0%, var(--card-shade) 100%);
  }
  .card--back .card__light { height: 46%; }
  .card--front .card__light { height: 40%; }

  .card__tan {
    position: absolute; left: 0; bottom: 0; width: 100%; height: 54%;
    background: var(--tan);
  }
  .card__red {
    position: absolute; left: 0; bottom: 0; width: 100%; height: 60%;
    background: var(--red);
  }

  .brand { position: absolute; display: flex; align-items: center; gap: 12px; }
  .brand__mark { width: 22px; height: 22px; background: var(--red); flex: none; }
  .brand__name {
    font-weight: 700; color: var(--red); text-transform: uppercase;
    font-size: 19px; line-height: 1.1; letter-spacing: .5px;
  }
  .card--back .brand { left: 200px; top: 68px; }
  .card--front .brand { left: 40px; top: 58px; }
  .card--front .brand__name { font-size: 16px; }

  .back__info { position: absolute; left: 40px; bottom: 36px; color: var(--white); }
  .back__tagline { font-size: 14px; letter-spacing: .6px; margin-bottom: 6px; }
  .back__web { font-size: 17px; letter-spacing: 1px; }

  .person { position: absolute; right: 40px; top: 46px; text-align: right; }
  .person__name {
    font-family: "Michroma", "Open Sans", sans-serif;
    font-size: 22px; color: var(--ink); letter-spacing: 1px;
  }
  .person__role {
    margin-top: 6px; font-size: 11px; color: var(--ink-soft);
    letter-spacing: 2px; text-transform: uppercase;
  }

  .contacts {
    position: absolute; left: 0; bottom: 0; width: 100%; height: 60%;
    display: grid; grid-template-columns: 215px 120px 285px; column-gap: 20px;
    justify-content: center; align-items: start;
    padding-top: 38px;
  }
  .contact { display: flex; flex-direction: column; align-items: center; gap: 16px; }
  .contact__icon {
    width: 50px; height: 50px; border-radius: 50%; background: var(--white);
    display: flex; align-items: center; justify-content: center;
  }
  .contact__icon svg { width: 26px; height: 26px; }
  .contact__text {
    color: var(--white); font-size: 13px; line-height: 1.6; text-align: center;
    letter-spacing: .3px; white-space: nowrap;
  }
</style>
</head>
<body>
<main class="canvas">

  <section class="card card--back" aria-label="Business card back">
    <div class="card__light"></div>
    <div class="card__tan"></div>
    <div class="brand">
      <span class="brand__mark"></span>
      <span class="brand__name">Brantwell Family<br>Eye Care</span>
    </div>
    <div class="back__info">
      <p class="back__tagline">Clearly the best for your vision.</p>
      <p class="back__web">www.brantwellfamilyeyecare.example</p>
    </div>
  </section>

  <section class="card card--front" aria-label="Business card front">
    <div class="card__light"></div>
    <div class="card__red"></div>
    <div class="brand">
      <span class="brand__mark"></span>
      <span class="brand__name">Brantwell Family<br>Eye Care</span>
    </div>
    <div class="person">
      <p class="person__name">DR. MARCUS VELBRIN</p>
      <p class="person__role">Optometrist</p>
    </div>

    <div class="contacts">
      <div class="contact">
        <span class="contact__icon">
          <svg viewBox="0 0 24 24" aria-hidden="true"><path d="M12 3 2 12h3v8h5v-5h4v5h5v-8h3z" fill="#c9363e"/></svg>
        </span>
        <p class="contact__text">7258 Dunmore Ridge Blvd #215<br>Brantwell, MO 64172</p>
      </div>
      <div class="contact">
        <span class="contact__icon">
          <svg viewBox="0 0 24 24" aria-hidden="true"><path d="M6.6 10.8a15 15 0 0 0 6.6 6.6l2.2-2.2c.3-.3.7-.4 1-.2 1.1.4 2.3.6 3.6.6.6 0 1 .4 1 1V20c0 .6-.4 1-1 1A17 17 0 0 1 3 4c0-.6.4-1 1-1h3.5c.6 0 1 .4 1 1 0 1.3.2 2.5.6 3.6.1.3 0 .7-.2 1z" fill="#c9363e"/></svg>
        </span>
        <p class="contact__text">(555) 382-9017</p>
      </div>
      <div class="contact">
        <span class="contact__icon">
          <svg viewBox="0 0 24 24" aria-hidden="true" fill="none" stroke="#c9363e" stroke-width="1.8"><circle cx="12" cy="12" r="9"/><ellipse cx="12" cy="12" rx="4" ry="9"/><path d="M3 12h18M5 7h14M5 17h14"/></svg>
        </span>
        <p class="contact__text">marc@brantwellfamilyeyecare.example<br>www.brantwellfamilyeyecare.example</p>
      </div>
    </div>
  </section>

</main>
</body>
</html>
```